I have a logo and need to design the business card and stationery.
Updates

The uploaded logo image named as GREYMARSH CONSTRUCTION which is to be replaced to GREYMARSH CONTRACTS. Kindly add below details and submit the designs- Company name- Greymarsh Engineering Contracts LLP Name & Post- Kelvan Joshi (Designated Partner) Address- Block No.317, Wing C, Tulvo Trade Court, Manek Pural Road, Ruparel Industrial Estate, Goregaon(E), Mumbai - 400 063 Contact- +91 97415 60382 Email- kelvanjoshi@mailbrook.example Website- www.greymarshcontracts.example Contact for Letterhead- +91-22-28754193

Hi Tovin Rahul, We are liking your Design #28860835. We have suggested some changes which are mentioned in feedback. Kindly revert with it asap to finalize this design.

Colors

Designer to choose colors to be used in the design.

```html
<!DOCTYPE html>
<html lang="en">
<head>
<meta charset="utf-8">
<title>Greymarsh Contracts — Letterhead</title>
<link rel="stylesheet" href="https://fonts.googleapis.com/css2?family=Open+Sans:wght@400;600;700&family=Lato:wght@400&display=swap">
<style>
  :root {
    --paper: #ffffff;
    --ink: #3a3a3a;
    --ink-strong: #2b2b2b;
    --ink-soft: #555555;
    --band-dark: #2e2e2e;
    --block-faint: #e8e8e8;
    --sign-fill: #ececec;
  }
  * { margin: 0; padding: 0; box-sizing: border-box; }
  html, body { width: 1040px; height: 1200px; overflow: hidden; background: var(--paper); }
  .letterhead {
    position: relative;
    width: 1040px; height: 1200px;
    background: var(--paper);
    font-family: "Open Sans", sans-serif;
    color: var(--ink);
    font-size: 15px;
    overflow: hidden;
  }
  .brand {
    position: absolute; right: 90px; top: 96px;
    display: flex; align-items: center; gap: 12px;
  }
  .brand-square { width: 26px; height: 26px; background: var(--ink-strong); }
  .brand-name {
    font-family: "Open Sans", sans-serif;
    font-weight: 700; font-size: 22px; letter-spacing: 1px;
    color: var(--ink-strong); line-height: 1.15;
  }
  .issue-date { position: absolute; left: 99px; top: 233px; }
  .recipient { position: absolute; left: 99px; top: 270px; line-height: 18px; }
  .salutation { position: absolute; left: 99px; top: 374px; }
  .body-copy {
    position: absolute; left: 99px; top: 420px; width: 842px;
    line-height: 27px; text-align: justify; hyphens: auto;
  }
  .body-copy p { margin-bottom: 27px; }
  .closing { position: absolute; left: 99px; top: 832px; }
  .signature {
    position: absolute; left: 99px; top: 870px; width: 240px; height: 30px;
    background: linear-gradient(90deg, var(--sign-fill), rgba(236,236,236,0));
  }
  .signer-name { position: absolute; left: 99px; top: 912px; font-size: 18px; color: var(--ink-strong); }
  .signer-role { position: absolute; left: 99px; top: 942px; font-size: 15px; }
  .corner-block {
    position: absolute; left: 573px; top: 798px; width: 467px; height: 402px;
    background: var(--block-faint);
  }
  .side-band {
    position: absolute; left: 0; top: 1010px; width: 76px; height: 190px;
    background: var(--band-dark);
  }
  .contact-list {
    position: absolute; left: 128px; top: 1088px; list-style: none;
    font-family: "Lato", sans-serif; font-size: 17px; color: var(--ink-strong);
    line-height: 22px;
  }
  .contact-list li { display: flex; align-items: center; gap: 10px; }
  .contact-list svg { width: 15px; height: 15px; fill: var(--ink-strong); }
</style>
</head>
<body>
<main class="letterhead">
  <header class="brand">
    <span class="brand-square"></span>
    <span class="brand-name">GREYMARSH<br>CONTRACTS</span>
  </header>

  <p class="issue-date">Issuing Date: May 5, 2018</p>
  <address class="recipient" style="font-style:normal">
    Name Of Employee Mr. XYZABC<br>Address of Employee<br>Address Line 2 etc..
  </address>

  <p class="salutation">Dear Mr.XYZABC</p>

  <section class="body-copy">
    <p>Lorem Ipsum has been the industry's standard dummy text ever since the 1500s, when an unknown printer took a galley of type and scrambled it to make a type specimen book. It has survived not only five centuries, but also the leap into electronic typesetting, remaining essentially unchanged. It was popularised in the 1960s with the release of Transfix sheets containing Lorem Ipsum passages, and more recently with desktop publishing software like Alden PageForm including versions of Lorem Ipsum.</p>
    <p>Lorem Ipsum is simply dummy text of the printing and typesetting industry. Lorem Ipsum has been the industry's standard dummy text ever since the 1500s, when an unknown printer took a galley of type and scrambled it to make a type specimen book.</p>
    <p>It has survived not only five centuries, but also the leap into electronic typesetting, remaining essentially unchanged. It was popularised in the 1960s with the release of Transfix sheets containing Lorem IpsumIpsum passages.</p>
  </section>

  <div class="corner-block"></div>

  <p class="closing">Yours Sincerely</p>
  <div class="signature" role="img" aria-label="Handwritten signature of Marlen Fosk"></div>
  <p class="signer-name">Marlen Fosk</p>
  <p class="signer-role">Managing Director</p>

  <div class="side-band"></div>

  <ul class="contact-list">
    <li>
      <svg viewBox="0 0 16 16" aria-hidden="true"><path d="M3 1h3l1.5 4-2 1.2a9 9 0 0 0 4.3 4.3L11 8.5l4 1.5v3a2 2 0 0 1-2 2A12 12 0 0 1 1 3a2 2 0 0 1 2-2z"/></svg>
      +91 97415 60382
    </li>
    <li>
      <svg viewBox="0 0 16 16" aria-hidden="true"><path d="M1 3h14v10H1z M2.5 4.5 8 9l5.5-4.5" fill="none" stroke="#2b2b2b" stroke-width="1.6"/></svg>
      kelvanjoshi@mailbrook.example
    </li>
    <li>
      <svg viewBox="0 0 16 16" aria-hidden="true"><circle cx="8" cy="8" r="6.5" fill="none" stroke="#2b2b2b" stroke-width="1.6"/><path d="M1.5 8h13M8 1.5c-3 3.5-3 9.5 0 13M8 1.5c3 3.5 3 9.5 0 13" fill="none" stroke="#2b2b2b" stroke-width="1.2"/></svg>
      www.greymarshcontracts.example
    </li>
  </ul>
</main>
</body>
</html>
```